Roofing Contractor business card redesign

I want to redesign my business card with a fresh, eye catching concept

Target Market(s)

Residential Roofing Clients, potential employees, and subcontractors.

Industry/Entity Type

Business

Colors

Designer to choose colors to be used in the design.

Requirements
Nice to have
• I just want something that's more pleasing to the eye. You can use a combination of either / or of my logos.

```html
<!DOCTYPE html>
<html lang="en">
<head>
<meta charset="utf-8">
<title>Steady Hands General Contractors – Business Card</title>
<link rel="stylesheet" href="https://fonts.googleapis.com/css2?family=Oswald:wght@500;600&family=Open+Sans:wght@400&display=swap">
<style>
  :root {
    --page-bg: #e9e6e3;
    --card-dark: #3b2120;
    --card-light: #f6f6f6;
    --brand-brown: #4a1d18;
    --text-light: #ffffff;
    --art-warm: #f3c23a;
    --art-orange: #e9782a;
    --art-ring: #ffffff;
  }
  * { margin: 0; padding: 0; box-sizing: border-box; }
  html, body { width: 1200px; height: 900px; overflow: hidden; }
  body {
    background: var(--page-bg);
    position: relative;
    font-family: "Open Sans", Arial, sans-serif;
  }
  .card {
    position: absolute;
    overflow: hidden;
    box-shadow: 0 6px 18px rgba(0,0,0,0.18);
  }
  .card-front {
    left: 78px; top: 35px;
    width: 588px; height: 363px;
    background: var(--card-dark);
    color: var(--text-light);
  }
  .crew-illustration {
    position: absolute;
    left: 322px; top: -12px;
    width: 390px; height: 390px;
    border-radius: 50%;
    border: 10px solid var(--art-ring);
    background: radial-gradient(circle at 55% 35%, var(--art-warm) 0%, #f7e3a6 30%, var(--art-orange) 62%, #8a4a2a 100%);
  }
  .holder-name {
    position: absolute;
    left: 29px; top: 48px;
    font-family: "Oswald", "Arial Narrow", sans-serif;
    font-weight: 500;
    font-size: 25px;
    letter-spacing: 0.2px;
  }
  .holder-titles {
    position: absolute;
    left: 29px; top: 83px;
    font-size: 15px;
    line-height: 21px;
  }
  .contact-list {
    position: absolute;
    left: 29px; top: 190px;
    list-style: none;
    font-size: 15px;
    line-height: 21.5px;
  }
  .contact-list li { display: flex; align-items: center; gap: 6px; }
  .contact-icon { width: 13px; height: 13px; fill: var(--text-light); flex: none; }
  .office-address {
    position: absolute;
    left: 29px; top: 292px;
    font-size: 15px;
    line-height: 21px;
    font-style: normal;
  }
  .card-back {
    left: 388px; top: 505px;
    width: 566px; height: 352px;
    background: var(--card-light);
  }
  .brand-lockup {
    position: absolute;
    left: 0; right: 0; top: 128px;
    display: flex; flex-direction: column; align-items: center;
    font-family: "Oswald", "Arial Narrow", sans-serif;
    font-weight: 600;
    color: var(--brand-brown);
  }
  .brand-name { display: flex; align-items: center; gap: 10px; font-size: 44px; line-height: 1; }
  .brand-dot { width: 34px; height: 34px; border-radius: 50%; background: var(--brand-brown); }
  .brand-tagline { font-size: 20px; margin-top: 12px; letter-spacing: 0.3px; }
</style>
</head>
<body>

<section class="card card-front">
  <div class="crew-illustration" role="img" aria-label="Illustrated roofing crew in hard hats holding hammers in front of a roof"></div>

  <h1 class="holder-name">Sam Whitford</h1>
  <p class="holder-titles">Halden certified Roof Inspector<br>Licensed Property Adjuster</p>

  <ul class="contact-list">
    <li>
      <svg class="contact-icon" viewBox="0 0 16 16"><path d="M2 5c0-2 1.5-3 6-3s6 1 6 3v1.5h-3V5H5v1.5H2zM4 7h8l2 6H2z"/></svg>
      (555) 210-4800
    </li>
    <li>
      <svg class="contact-icon" viewBox="0 0 16 16"><path d="M4.5 0h7a1 1 0 0 1 1 1v14a1 1 0 0 1-1 1h-7a1 1 0 0 1-1-1V1a1 1 0 0 1 1-1zm1 2v10h5V2zm2.5 11a1 1 0 1 0 0 2 1 1 0 0 0 0-2z"/></svg>
      (555) 318-7262
    </li>
    <li>
      <svg class="contact-icon" viewBox="0 0 16 16"><path d="M0 3h16v10H0zm1.5 1.2v.3L8 9l6.5-4.5v-.3zM1.5 6v5.5h13V6L8 10.5z"/></svg>
      sam@steadyhandstx.com
    </li>
    <li>
      <svg class="contact-icon" viewBox="0 0 16 16"><circle cx="8" cy="8" r="7.5"/><path d="M8 1v14M1 8h14M3 4h10M3 12h10" stroke="#3b2120" stroke-width="1" fill="none"/></svg>
      www.SteadyHandsGC.com
    </li>
  </ul>

  <address class="office-address">4410 Meadow Lane Suite 108<br>Fairview, TX 75000</address>
</section>

<section class="card card-back">
  <div class="brand-lockup">
    <div class="brand-name"><span class="brand-dot"></span>Steady Hands</div>
    <div class="brand-tagline">General Contractors, Inc.</div>
  </div>
</section>

</body>
</html>
```